Brevlon Website Design - Wordpress

Need a website WordPress design for our existing website that we just stood up. The logo is already in place and name. Brevlon.example We are a company which makes connections with our clients through educating them and providing networking events. We would like for the website to show a VIP/special feel to it.

Target Market(s)

Business executives and employees. Age group 26-65 in the following sectors:
- Technology
- Human Resources
- Finance
- Sales

Industry/Entity Type

Technical Service

Number of Pages Required

4 page

Font styles to use
Sans Serif

Requirements
Must have
• Must be something for Wordpress
Nice to have
• Would like this to be professional but look cutting edge and VIP.

```html
<!DOCTYPE html>
<html lang="en">
<head>
<meta charset="utf-8">
<title>Brevlon Connected</title>
<link href="https://fonts.googleapis.com/css2?family=Montserrat:wght@400;500;600&family=Open+Sans:wght@400;600&display=swap" rel="stylesheet">
<style>
:root{
  --bg-top:#000000;
  --bg-main:#121212;
  --card:#161616;
  --green:#3d9b3f;
  --white:#ffffff;
  --muted:#8a8a8a;
  --dim:#5e5e5e;
  --mind:#1a6a9a;
  --soul:#7b3f95;
  --heart:#c8262c;
  --strength:#e0a820;
}
*{margin:0;padding:0;box-sizing:border-box}
html,body{width:1200px;height:2510px;overflow:hidden;background:var(--bg-main)}
body{position:relative;font-family:"Open Sans",Arial,sans-serif;color:var(--white)}
.abs{position:absolute}
.backdrop{left:0;top:0;width:1200px;height:2510px}
.brand{left:80px;top:38px;display:flex;align-items:center;gap:14px}
.brand-mark{width:40px;height:40px;background:var(--green)}
.brand-name{font-family:"Montserrat",sans-serif;font-weight:400;font-size:30px;letter-spacing:4px;color:var(--white)}
.nav{right:80px;top:44px;display:flex;gap:30px;font-family:"Montserrat",sans-serif;font-size:14px;font-weight:500}
.nav a{color:var(--white);text-decoration:none;position:relative}
.nav a.active::before{content:"";position:absolute;left:0;top:-10px;width:22px;height:2px;background:var(--white)}
.hero-title{left:80px;top:222px;font-family:"Montserrat",sans-serif;font-weight:500;font-size:42px;color:var(--green)}
.hero-sub{left:80px;top:290px;font-size:19px}
.hero-text{left:80px;top:340px;width:470px;font-size:14.5px;line-height:1.75}
.hero-photo{left:645px;top:145px;width:335px;height:330px;background:linear-gradient(135deg,#555,#2a2a2a 60%,#1a1a1a)}
.laptop-photo{left:200px;top:775px;width:520px;height:295px;border-radius:14px;background:linear-gradient(160deg,#d8d8d8,#6d6258 30%,#3a3430 70%,#bdbdbd)}
.pillar{display:flex;align-items:center;gap:16px;font-family:"Montserrat",sans-serif}
.pillar .dot{width:62px;height:62px;border-radius:50%;display:flex;align-items:center;justify-content:center}
.pillar .name{font-size:18px;font-weight:500;color:#a0a0a0;letter-spacing:.5px}
.pillar .sub{font-family:"Open Sans",sans-serif;font-size:13px;color:#666;margin-top:8px}
.offer-title{left:0;top:1138px;width:1200px;text-align:center;font-family:"Montserrat",sans-serif;font-weight:600;font-size:36px;color:var(--green)}
.cards{left:79px;top:1222px;display:flex;gap:6px}
.card{width:257px;height:310px;background:var(--card);box-shadow:0 6px 22px rgba(0,0,0,.7);text-align:center;padding-top:50px}
.card svg{display:block;margin:0 auto}
.card h3{margin-top:24px;font-family:"Montserrat",sans-serif;font-weight:500;font-size:19px;color:var(--green);letter-spacing:.5px}
.card p{margin:18px auto 0;width:215px;font-size:13px;line-height:25px;color:var(--dim)}
.btn{display:flex;align-items:center;justify-content:center;background:var(--green);color:var(--white);font-family:"Montserrat",sans-serif;font-weight:600;font-size:17px;letter-spacing:.5px}
.btn-value{left:507px;top:1595px;width:186px;height:51px}
.event-title{left:80px;top:1858px;font-family:"Montserrat",sans-serif;font-weight:500;font-size:42px;color:var(--green)}
.event-meta{left:80px;top:1934px;font-size:19px}
.btn-connect{left:934px;top:1875px;width:186px;height:52px;font-weight:500;font-size:19px}
.contact{top:2230px;text-align:center;font-size:13px;color:#707070}
.contact svg{display:block;margin:0 auto 14px}
.socials{left:502px;top:2238px;display:flex;gap:10px}
.socials span{width:42px;height:42px;border-radius:4px}
.divider{top:2258px;width:1px;height:34px;background:#666}
.foot-nav{left:0;top:2382px;width:1200px;display:flex;justify-content:center;gap:24px;font-size:13px;color:#6a6a6a}
.foot-nav i{font-style:normal;color:#444}
.foot-line{left:0;top:2439px;width:1200px;height:1px;background:#262626}
.copy{left:0;top:2463px;width:1200px;text-align:center;font-size:13px;color:#6a6a6a}
</style>
</head>
<body>

<svg class="abs backdrop" viewBox="0 0 1200 2510" aria-hidden="true">
  <path d="M0 0H1200V548C1090 530 1000 540 860 575C700 615 520 590 360 620C220 645 80 660 0 620Z" fill="var(--bg-top)"/>
  <circle cx="720" cy="887" r="150" fill="none" stroke="#050505" stroke-width="12"/>
</svg>

<div class="abs brand"><span class="brand-mark"></span><span class="brand-name">BREVLON</span></div>
<nav class="abs nav"><a class="active">EVENTS</a><a>EXPAND</a><a>X</a><a>ABOUT</a><a>CONNECT</a></nav>

<h1 class="abs hero-title">Expand Your Business</h1>
<p class="abs hero-sub">It's about our unique X Strategy</p>
<p class="abs hero-text">BREVLON provides impactful connection opportunities to help educate, equip and expand you and your business</p>
<div class="abs hero-photo" role="img" aria-label="Photo of a smiling businesswoman holding a tablet"></div>

<div class="abs laptop-photo" role="img" aria-label="Laptop showing a team meeting photo"></div>

<div class="abs pillar" style="left:734px;top:717px"><span class="dot" style="background:var(--mind)"><svg width="26" height="26" viewBox="0 0 26 26"><circle cx="13" cy="13" r="10" fill="#fff"/></svg></span><div><div class="name">MIND</div><div class="sub">Thought</div></div></div>
<div class="abs pillar" style="left:799px;top:801px"><span class="dot" style="background:var(--soul)"><svg width="26" height="26" viewBox="0 0 26 26"><path d="M13 3L22 13 13 23 4 13Z" fill="#fff"/></svg></span><div><div class="name">SOUL</div><div class="sub">Intuition</div></div></div>
<div class="abs pillar" style="left:811px;top:906px"><span class="dot" style="background:var(--heart)"><svg width="28" height="26" viewBox="0 0 28 26"><path d="M14 24L3 13A6 6 0 0 1 14 6 6 6 0 0 1 25 13Z" fill="#fff"/></svg></span><div><div class="name">HEART</div><div class="sub">Emotion</div></div></div>
<div class="abs pillar" style="left:751px;top:999px"><span class="dot" style="background:var(--strength)"><svg width="26" height="26" viewBox="0 0 26 26"><circle cx="13" cy="11" r="8" fill="#fff"/><rect x="9" y="19" width="8" height="5" fill="#fff"/></svg></span><div><div class="name">STREANTH</div><div class="sub">Energy</div></div></div>

<h2 class="abs offer-title">What we offer you</h2>
<div class="abs cards">
  <div class="card">
    <svg width="76" height="52" viewBox="0 0 76 52"><path d="M38 2L74 18 38 34 2 18Z" fill="var(--green)"/><path d="M16 26V42C26 50 50 50 60 42V26L38 36Z" fill="var(--green)"/></svg>
    <h3>EDUCATE</h3><p>At BREVLON, we provide effective training and learning as the foundation for building a healthy, successful company.</p>
  </div>
  <div class="card">
    <svg width="64" height="56" viewBox="0 0 64 56"><path d="M6 40L26 8 40 16 30 30 44 22 58 34 34 54Z" fill="var(--green)"/></svg>
    <h3>EQUIP</h3><p>Through our connected ecosystem of companies, we'll help find the right partners for equipping you to move forward.</p>
  </div>
  <div class="card">
    <svg width="52" height="52" viewBox="0 0 52 52"><rect width="52" height="52" rx="4" fill="var(--green)"/><path d="M12 19H38M32 13L38 19 32 25M40 33H14M20 27L14 33 20 39" stroke="#161616" stroke-width="4" fill="none"/></svg>
    <h3>EXCHANGE</h3><p>We connect you with others who have successfully implemented our X Strategy to facilitate growth in their business.</p>
  </div>
  <div class="card">
    <svg width="54" height="54" viewBox="0 0 54 54"><rect x="2" y="2" width="50" height="50" fill="none" stroke="var(--green)" stroke-width="4"/><path d="M12 12L42 42M42 12L12 42M12 12H22M12 12V22M42 12H32M42 12V22M12 42H22M12 42V32M42 42H32M42 42V32" stroke="var(--green)" stroke-width="4" fill="none"/></svg>
    <h3>EXPAND</h3><p>Our goal is to help you and your business increase productivity and scale through effective strategy and healthy culture.</p>
  </div>
</div>

<div class="abs btn btn-value">X = VALUE</div>

<svg class="abs" style="left:0;top:1736px" width="1200" height="400" viewBox="0 0 1200 400" role="img" aria-label="Photo of colleagues smiling around a laptop in an office">
  <defs><linearGradient id="eventShade" x1="0" y1="0" x2="1" y2="0"><stop offset="0" stop-color="#1c2530"/><stop offset=".55" stop-color="#39414a"/><stop offset="1" stop-color="#2a2f36"/></linearGradient></defs>
  <path d="M0 20C300 -8 900 -8 1200 20V240C1000 330 820 400 600 400 380 400 200 330 0 240Z" fill="url(#eventShade)"/>
</svg>
<h2 class="abs event-title">Expand Your Business</h2>
<p class="abs event-meta">March 21, 2019 &nbsp;&nbsp;|&nbsp;&nbsp; Denver, Colorado</p>
<div class="abs btn btn-connect">CONNECT</div>

<div class="abs contact" style="left:160px;width:160px">
  <svg width="40" height="40" viewBox="0 0 40 40"><path d="M10 3L16 12 12 16C14 22 18 26 24 28L28 24 37 30 32 37C18 36 4 22 3 8Z" fill="none" stroke="var(--green)" stroke-width="2.5"/></svg>
  1-855-555-0199
</div>
<div class="abs divider" style="left:420px"></div>
<div class="abs socials" aria-label="Social links">
  <span style="background:#3b5a98"></span><span style="background:#1f9be8"></span><span style="background:#3f6a8f"></span><span style="background:#0d73a8"></span>
</div>
<div class="abs divider" style="left:780px"></div>
<div class="abs contact" style="left:856px;width:200px">
  <svg width="44" height="32" viewBox="0 0 44 32"><rect x="2" y="2" width="40" height="28" fill="none" stroke="var(--green)" stroke-width="2.5"/><path d="M2 2L22 18 42 2M2 30L17 14M42 30L27 14" fill="none" stroke="var(--green)" stroke-width="2.5"/></svg>
  connect@brevlon.example
</div>

<div class="abs foot-nav"><span>Events</span><i>|</i><span>Expands</span><i>|</i><span>X</span><i>|</i><span>About</span><i>|</i><span>Connect</span></div>
<div class="abs foot-line"></div>
<p class="abs copy">©BREVLON. 2019 - All Rights Reserved.</p>

</body>
</html>
```